Need help in designing new business card utilizing our new logo.

BuildMark Solutions works with Construction Business Owners, Managers & IT Professionals to strengthen software usage and increase user productivity.

Our Construction Accounting and Mobile Field Management Software Clients engage with us in the following areas:

New Software Implementations
Software Re-Implementations
Redesigning Software Usage at the User Level
Project Coordination & Management
Continued Software Support

Old tag line:
Clear Choices - Dependable Results

www.buildmark-solutions.example

Ridge 4 is a product, but not needed for a new business card.

```html
<!DOCTYPE html>
<html lang="en">
<head>
<meta charset="utf-8">
<title>BuildMark Solutions – Business Card</title>
<link rel="stylesheet" href="https://fonts.googleapis.com/css2?family=Roboto:wght@400;500&family=Roboto+Condensed:wght@700&display=swap">
<style>
  :root {
    --brand-blue: #0d1a9c;
    --card-white: #f3f3f3;
    --text-dark: #3a3a3a;
    --rule-grey: #a8a8a8;
    --stage: #b3b3b3;
  }
  * { margin: 0; padding: 0; box-sizing: border-box; }
  html, body { width: 1200px; height: 576px; overflow: hidden; }
  body {
    background: var(--stage);
    position: relative;
    font-family: "Roboto", Arial, sans-serif;
  }
  .card {
    position: absolute;
    background: var(--card-white);
    border-radius: 12px;
    overflow: hidden;
    box-shadow: 0 3px 6px rgba(0,0,0,0.25);
  }
  .card--front { left: 82px; top: 138px; width: 484px; height: 294px; }
  .card--back  { left: 602px; top: 138px; width: 481px; height: 292px; }

  /* name-mark block */
  .brand {
    position: absolute;
    display: flex;
    align-items: center;
    gap: 12px;
    color: var(--brand-blue);
    font-weight: 500;
  }
  .brand__square { width: 44px; height: 44px; background: var(--brand-blue); flex: none; }
  .brand__text { display: flex; flex-direction: column; line-height: 1; }
  .brand__name { font-size: 36px; letter-spacing: 0.5px; }
  .brand__sub { font-size: 15px; letter-spacing: 8.6px; margin-top: 4px; }
  .card--front .brand { left: 50%; top: 56px; transform: translateX(-50%); }
  .card--back .brand { right: 22px; top: 46px; }
  .card--back .brand__name { font-size: 32px; }
  .card--back .brand__sub { font-size: 13.5px; letter-spacing: 7.6px; }

  .services {
    position: absolute; left: 0; top: 168px; width: 100%; height: 80px;
    background: var(--brand-blue);
    color: #fff;
    font-size: 13px;
    line-height: 18px;
    text-align: center;
    padding-top: 13px;
  }
  .services .sep { margin: 0 8px; }
  .website-front {
    position: absolute; left: 0; top: 262px; width: 100%;
    text-align: center; font-size: 12px; color: var(--brand-blue);
  }
  .website-front::before, .website-front::after {
    content: ""; display: inline-block; width: 40px; height: 1px;
    background: var(--rule-grey); vertical-align: middle; margin: 0 18px;
  }

  .edge-tab {
    position: absolute; left: -22px; top: 136px; width: 30px; height: 48px;
    border-radius: 50%; background: var(--brand-blue);
  }
  .person { position: absolute; left: 20px; top: 136px; right: 22px; }
  .person__name {
    font-family: "Roboto Condensed", Arial, sans-serif;
    font-weight: 700; font-size: 21px; color: var(--brand-blue); line-height: 1;
  }
  .person__role {
    display: flex; align-items: flex-end; gap: 4px;
    font-size: 11.5px; color: var(--text-dark); margin-top: 5px;
  }
  .person__role::after { content: ""; flex: 1; height: 1px; background: var(--rule-grey); margin-bottom: 3px; }

  .contacts { position: absolute; left: 20px; top: 192px; list-style: none; font-size: 11.5px; color: var(--text-dark); }
  .contacts li { display: flex; align-items: center; gap: 10px; height: 17.5px; }
  .contacts svg { width: 11px; height: 11px; fill: var(--brand-blue); flex: none; }
  .contacts .accent { color: var(--brand-blue); }

  .address {
    position: absolute; right: 22px; top: 216px;
    text-align: right; font-size: 11.5px; line-height: 17px; color: var(--text-dark);
    font-style: normal;
  }
  .tagline {
    position: absolute; right: 0; bottom: 0; width: 280px; height: 30px;
    background: var(--brand-blue); color: #fff; font-size: 12px;
    clip-path: polygon(12px 0, 100% 0, 100% 100%, 0 100%);
    border-top-left-radius: 8px;
    display: flex; align-items: center; justify-content: flex-end; padding-right: 22px;
  }
</style>
</head>
<body>
  <section class="card card--front">
    <div class="brand">
      <span class="brand__square"></span>
      <span class="brand__text"><span class="brand__name">BUILDMARK</span><span class="brand__sub">SOLUTIONS</span></span>
    </div>
    <div class="services">
      <p>New Software Implementations<span class="sep">|</span>Software Re-Implementations</p>
      <p>Redesigning Software Usage at the User Level</p>
      <p>Project Coordination &amp; Management<span class="sep">|</span>Continued Software Support</p>
    </div>
    <p class="website-front">www.buildmark-solutions.example</p>
  </section>

  <section class="card card--back">
    <div class="brand">
      <span class="brand__square"></span>
      <span class="brand__text"><span class="brand__name">BUILDMARK</span><span class="brand__sub">SOLUTIONS</span></span>
    </div>
    <span class="edge-tab"></span>
    <div class="person">
      <h1 class="person__name">Dana R. Whitfield</h1>
      <p class="person__role">Owner</p>
    </div>
    <ul class="contacts">
      <li><svg viewBox="0 0 12 12"><path d="M3 0h6a1 1 0 0 1 1 1v10a1 1 0 0 1-1 1H3a1 1 0 0 1-1-1V1a1 1 0 0 1 1-1zm.8 1.5v7.5h4.4V1.5z"/></svg>555-014-2281</li>
      <li><svg viewBox="0 0 12 12"><path d="M0 4c0-2 3-3 6-3s6 1 6 3v1H9V3.8H3V5H0zM2 6h8l1 5H1z"/></svg>800-555-0147 ext. 100</li>
      <li><svg viewBox="0 0 12 12"><path d="M0 2h12v1L6 7 0 3zM0 4.2l6 4 6-4V10H0z"/></svg>dana.whitfield@buildmark-solutions.example</li>
      <li><svg viewBox="0 0 12 12"><path d="M6 0a6 6 0 1 0 0 12A6 6 0 0 0 6 0zm0 1.2c.7.8 1.2 2 1.4 3.3H4.6C4.8 3.2 5.3 2 6 1.2zM1.3 5.5h2.2c0 1.2.3 2.4.8 3.3A4.8 4.8 0 0 1 1.3 5.5zm3.3 0h2.8C7.3 7 6.8 8.3 6 9.3 5.2 8.3 4.7 7 4.6 5.5zm3.9 0h2.2a4.8 4.8 0 0 1-3 3.3c.5-.9.8-2.1.8-3.3z"/></svg><span>www.<span class="accent">buildmark-solutions</span>.example</span></li>
    </ul>
    <address class="address">
      14B Meadow Lane - PMB 118<br>Harbor Falls, NY 12000
    </address>
    <p class="tagline">Clear Choices - Dependable Results</p>
  </section>
</body>
</html>
```